Modern Attractive Letterhead for Veterinary House Call Business.

A letterhead which can be printed on A4, A5 and A6 paper sizes.
To have: ( our files to be uploaded)
1. Logo with Text
2. telephone
3. email
4. website
5. Address

Target Market(s)

60-85year mainly women pet owners. Also market include families, young professionals, busy people who have dogs and cats

Industry/Entity Type

Business

Requirements
Must have
• 1. Logo with Text ( provided)
• 2. telephone
• 3. email
• 4. website
• 5. Address
Nice to have
• Needs to be modern, preferably warm and caring in nature( if possible )
Should not have
• difficulty in printing A5 and A6

```html
<!DOCTYPE html>
<html lang="en">
<head>
<meta charset="utf-8">
<title>Rosewood Pet Care — Letterhead</title>
<link rel="stylesheet" href="https://fonts.googleapis.com/css2?family=Cinzel:wght@400;600&display=swap">
<style>
  :root {
    --backdrop: #e8e6e2;
    --paper-top: #ffffff;
    --paper-bottom: #f3f4f6;
    --band-light: #29a8df;
    --band-mid: #2b6fae;
    --band-navy: #27235d;
    --accent-green: #3b9a3e;
    --text-dark: #2a2a36;
    --rule-grey: #9a9aa4;
  }
  * { margin: 0; padding: 0; box-sizing: border-box; }
  html, body {
    width: 948px;
    height: 1200px;
    overflow: hidden;
    background: var(--backdrop);
  }
  .letterhead {
    position: absolute;
    left: 43px;
    top: 43px;
    width: 862px;
    height: 1114px;
    background: linear-gradient(160deg, var(--paper-top) 40%, var(--paper-bottom) 100%);
    box-shadow: 0 1px 4px rgba(0,0,0,0.18);
    font-family: "Cinzel", serif;
    color: var(--text-dark);
  }
  .side-band {
    position: absolute;
    left: 0;
    top: 0;
    width: 94px;
    height: 100%;
    background: linear-gradient(to bottom,
      var(--band-light) 0%,
      var(--band-mid) 28%,
      var(--band-navy) 52%,
      var(--band-navy) 100%);
  }
  .side-rule {
    position: absolute;
    left: 101px;
    top: 0;
    width: 2px;
    height: 100%;
    background: var(--accent-green);
  }
  .brand {
    position: absolute;
    left: 66px;
    top: 48px;
    display: flex;
    align-items: center;
    gap: 16px;
  }
  .brand-mark {
    width: 62px;
    height: 62px;
    border-radius: 50%;
    background: var(--band-light);
    border: 4px solid #ffffff;
    flex-shrink: 0;
  }
  .brand-name {
    color: var(--band-navy);
    font-size: 30px;
    font-weight: 600;
    line-height: 1;
    letter-spacing: 0.5px;
    white-space: nowrap;
  }
  .postal-address {
    position: absolute;
    left: 611px;
    top: 60px;
    padding-left: 10px;
    border-left: 1px solid var(--rule-grey);
    font-size: 15px;
    line-height: 20px;
    font-style: normal;
  }
  .contact-list {
    position: absolute;
    left: 108px;
    top: 1040px;
    list-style: none;
    font-size: 13px;
    line-height: 20px;
  }
  .contact-list li {
    display: flex;
    align-items: center;
    gap: 6px;
  }
  .contact-list svg {
    width: 12px;
    height: 12px;
    flex-shrink: 0;
  }
</style>
</head>
<body>
  <main class="letterhead">
    <div class="side-band"></div>
    <div class="side-rule"></div>

    <header class="brand">
      <span class="brand-mark"></span>
      <h1 class="brand-name">Rosewood Pet Care</h1>
    </header>

    <address class="postal-address">
      PO Box 4410 Fernvale<br>
      QLD 4306
    </address>

    <ul class="contact-list">
      <li>
        <svg viewBox="0 0 12 12" aria-hidden="true">
          <path d="M3 1 L5 3.5 L4 5 Q5 7 7 8 L8.5 7 L11 9 L9.5 11 Q4 10.5 1 3 Z" fill="none" stroke="#3b9a3e" stroke-width="1.2" stroke-linejoin="round"/>
        </svg>
        0491555203
      </li>
      <li>
        <svg viewBox="0 0 12 12" aria-hidden="true">
          <rect x="1" y="3" width="10" height="7" rx="1" fill="#3b9a3e"/>
          <path d="M1.5 3.5 L6 7 L10.5 3.5" fill="none" stroke="#ffffff" stroke-width="1"/>
        </svg>
        HELLO@ROSEWOODPETCARE.COM.AU
      </li>
      <li>
        <svg viewBox="0 0 12 12" aria-hidden="true">
          <circle cx="6" cy="6" r="5" fill="#3b9a3e"/>
          <ellipse cx="6" cy="6" rx="2.2" ry="5" fill="none" stroke="#ffffff" stroke-width="0.8"/>
          <line x1="1" y1="6" x2="11" y2="6" stroke="#ffffff" stroke-width="0.8"/>
        </svg>
        WWW.ROSEWOODPETCARE.COM.AU
      </li>
    </ul>
  </main>
</body>
</html>
```